Modern Business Card

Modern professional business card with more than just logo and demographic info. Something memorable.

We are a trendy/modern chiropractic group with an emphasis on neurology, hence the minimalist-type brain logo. We want to convey that modern and technical aspect with professionalism and the elite nature of our practice environment.

```html
<!DOCTYPE html>
<html lang="en">
<head>
<meta charset="utf-8">
<title>Cadence Chiropractic — Business Card</title>
<link rel="stylesheet" href="https://fonts.googleapis.com/css2?family=Tinos&family=Exo+2:wght@400;500&display=swap">
<style>
  :root {
    --backdrop: #1e1e1f;
    --card: #0a0a0b;
    --pattern-dark: #101011;
    --pattern-light: #1b1b1d;
    --white: #ffffff;
    --grey: #7a7a7c;
    --grey-light: #a9a9ab;
    --blue: #3f7fcf;
    --rule: #e8e8e8;
  }
  * { box-sizing: border-box; margin: 0; padding: 0; }
  html, body { width: 1200px; height: 900px; overflow: hidden; }
  body {
    background: var(--backdrop);
    position: relative;
    font-family: "Exo 2", sans-serif;
  }
  .card {
    position: absolute;
    left: 280px;
    width: 640px;
    height: 366px;
    background: var(--card);
    box-shadow: 0 10px 30px rgba(0,0,0,0.55);
    overflow: hidden;
  }
  .card--back { top: 48px; }
  .card--front { top: 470px; }

  /* back side */
  .pattern-field {
    position: absolute; inset: 0;
    background: linear-gradient(135deg, var(--pattern-light), var(--pattern-dark) 55%, var(--pattern-light));
  }
  .back-mark {
    position: absolute;
    left: 302px; top: 118px;
    width: 36px; height: 36px;
    background: var(--blue);
  }
  .back-name {
    position: absolute;
    left: 0; right: 0; top: 268px;
    text-align: center;
    font-family: "Tinos", serif;
    color: var(--white);
    line-height: 1;
  }
  .back-name__main { display: block; font-size: 32px; letter-spacing: 1px; }
  .back-name__sub { display: block; font-size: 15px; letter-spacing: 1.5px; margin-top: 2px; }

  /* front side */
  .brand {
    position: absolute;
    left: 46px; top: 120px;
    display: flex; align-items: center; gap: 14px;
  }
  .brand__mark { width: 40px; height: 40px; background: var(--blue); border-radius: 50%; }
  .brand__name {
    font-family: "Tinos", serif;
    color: var(--white);
    line-height: 1;
  }
  .brand__main { display: block; font-size: 38px; letter-spacing: 1px; }
  .brand__sub { display: block; font-size: 18px; letter-spacing: 1.5px; margin-top: 2px; }

  .person {
    position: absolute;
    left: 370px; top: 176px;
    width: 250px;
  }
  .person__name {
    font-family: "Tinos", serif;
    font-size: 26px;
    color: var(--grey);
    letter-spacing: 1px;
    line-height: 1;
  }
  .person__title {
    font-size: 19px;
    color: var(--blue);
    margin-top: 4px;
  }
  .person__rule {
    height: 2px;
    background: var(--rule);
    width: 234px;
    margin: 14px 0 12px;
  }
  .contact { list-style: none; }
  .contact__item {
    display: flex; align-items: center; gap: 10px;
    font-size: 17px;
    color: var(--grey-light);
    line-height: 1.45;
  }
  .contact__icon { width: 16px; height: 16px; flex: none; }
  .contact__accent { color: var(--blue); font-weight: 500; }
</style>
</head>
<body>

  <section class="card card--back" aria-label="Card back">
    <div class="pattern-field" role="img" aria-label="Dark repeating brand pattern across the card"></div>
    <div class="back-mark"></div>
    <h1 class="back-name">
      <span class="back-name__main">CADENCE</span>
      <span class="back-name__sub">CHIROPRACTIC</span>
    </h1>
  </section>

  <section class="card card--front" aria-label="Card front">
    <div class="brand">
      <div class="brand__mark"></div>
      <div class="brand__name">
        <span class="brand__main">CADENCE</span>
        <span class="brand__sub">CHIROPRACTIC</span>
      </div>
    </div>

    <div class="person">
      <p class="person__name">MARCUS DELANEY</p>
      <p class="person__title">Training Specialist</p>
      <div class="person__rule"></div>
      <ul class="contact">
        <li class="contact__item">
          <svg class="contact__icon" viewBox="0 0 16 16" fill="none" stroke="var(--blue)" stroke-width="1.4">
            <circle cx="8" cy="8" r="7"/>
            <path d="M5.5 4.5 L7 6 L6.2 7.2 Q7.2 9 8.8 9.8 L10 9 L11.5 10.5 L10.5 11.5 Q6.5 11 4.5 5.5 Z" fill="var(--blue)" stroke="none"/>
          </svg>
          <span>555.014.2290</span>
        </li>
        <li class="contact__item">
          <svg class="contact__icon" viewBox="0 0 16 16" fill="none" stroke="var(--blue)" stroke-width="1.4">
            <rect x="1" y="3.5" width="14" height="9"/>
            <path d="M1 3.5 L8 9 L15 3.5"/>
          </svg>
          <span>m.delaney@cadencechiro.com</span>
        </li>
        <li class="contact__item">
          <svg class="contact__icon" viewBox="0 0 16 16" fill="none" stroke="var(--blue)" stroke-width="1.4">
            <circle cx="8" cy="8" r="7"/>
            <ellipse cx="8" cy="8" rx="3" ry="7"/>
            <path d="M1 8 H15 M2.5 4.5 H13.5 M2.5 11.5 H13.5"/>
          </svg>
          <span>www.<span class="contact__accent">cadencechiro</span>.com</span>
        </li>
      </ul>
    </div>
  </section>

</body>
</html>
```